K7 Electrical Services Ltd Web design

I require a web site for my new electrical contracting company. We are customer service orientated. Offering high value electrical installations, design and maintenance. Focused on custom residential and commercial upgrading. Lighting design and application are paramount in our company's services. Industry leading product use and integration are always on the forefront with our customer client services. As well as energy efficiency.

Target Market(s)

Homebuilders, General Contractors, Property management companies, clients, individuals,

Industry/Entity Type

Electric Company

Coding

Coded - Design and coding required

Number of Pages Required

3 page

Requirements
Must have
• Classic, modern, edgy but not trendy . Appeals to the masse.
• 3 page
• home page
• about page
• gallery page
• ability to contact from the webiste
Nice to have
• open to all types of designs that are relative to the construction industry.
• Black, Grey, metallic ice blue and deep purple colours from the logo.
Should not have
• anything cheesy with cartoon light bulb images.

```html
<!DOCTYPE html>
<html lang="en">
<head>
<meta charset="utf-8">
<title>K7 Electrical Services Ltd</title>
<link href="https://fonts.googleapis.com/css2?family=Exo+2:wght@500;600;700&family=Open+Sans:wght@400;600;700&display=swap" rel="stylesheet">
<style>
:root{
  --purple:#6c2fab;
  --purple-deep:#4d1d82;
  --purple-light:#8a4cc8;
  --ink:#0b0710;
  --night:#1a0f27;
  --white:#ffffff;
  --text:#3a3a3a;
  --muted:#c9c0d6;
  --footer:#050505;
}
*{margin:0;padding:0;box-sizing:border-box}
html,body{width:1200px;height:3509px;overflow:hidden}
body{position:relative;font-family:"Open Sans",Arial,sans-serif;color:var(--text);background:var(--white)}
.abs{position:absolute}
.heading{font-family:"Exo 2","Trebuchet MS",sans-serif;font-weight:600;letter-spacing:.5px}
section{position:absolute;left:0;width:1200px;overflow:hidden}
.mark{font-family:"Exo 2",sans-serif;font-weight:700;color:var(--purple);font-size:34px;line-height:1}
.mark-row{position:absolute;left:0;width:1200px;display:flex;justify-content:center;align-items:center;gap:18px}
.mark-row .rule{width:130px;height:1px;background:#b9a6cf}
.mark-row.on-dark .rule{background:rgba(255,255,255,.5)}
.mark-row.on-dark .mark{color:#d7cfe2}

/* hero */
.hero{top:0;height:604px;background:var(--ink)}
.hero-photo{left:0;top:120px;width:760px;height:484px;background:radial-gradient(ellipse at 30% 55%,#2b3550 0%,#121626 45%,var(--ink) 80%)}
.nav-logo{left:78px;top:14px;color:#d9d9d9;font-size:40px;line-height:1}
.nav{left:0;top:18px;width:1200px;height:30px}
.nav a{position:absolute;color:var(--white);font-size:15px;text-decoration:none;text-transform:uppercase}
.nav a.active{border-bottom:3px solid var(--purple-light);padding-bottom:8px}
.nav .phone{left:964px;font-weight:600;font-size:16px;display:flex;gap:6px;align-items:center}
.hero-title{left:66px;top:226px;font-size:38px;line-height:46px;color:var(--white);font-weight:700}
.hero-title span{color:#9a55dd}
.hero-text{left:66px;top:324px;width:460px;color:var(--white);font-size:14px;line-height:20px}
.btn-learn{left:66px;top:393px;width:142px;height:40px;background:var(--purple);color:var(--white);font-size:15px;display:flex;align-items:center;justify-content:center}
.hero-logo{left:643px;top:239px;width:297px;height:150px;background:var(--white);display:flex;align-items:center;justify-content:center;font-family:"Exo 2",sans-serif;font-weight:700;color:var(--purple);font-size:30px;text-align:center;line-height:1.15}

/* about */
.about{top:604px;height:484px;background:var(--white);text-align:center}
.about h2{position:absolute;top:148px;width:100%;font-size:31px;color:#333}
.about .divider{position:absolute;top:208px;left:460px;width:280px;height:1px;background:#bbb}
.about p{position:absolute;top:240px;left:135px;width:930px;font-size:17px;line-height:28px;color:#444}
.btn-outline{position:absolute;top:343px;left:523px;width:154px;height:42px;border:2px solid #222;font-weight:700;font-size:15px;display:flex;align-items:center;justify-content:center;color:#111;letter-spacing:.5px}
.callus{position:absolute;top:414px;width:100%;font-size:19px;color:#333;letter-spacing:1px}
.callus b{font-family:"Exo 2",sans-serif;font-weight:600}

/* contact form */
.contact{top:1088px;height:414px;background:var(--night)}
.contact-icon{left:168px;top:72px;width:80px;height:80px;border-radius:50%;background:var(--purple);display:flex;align-items:center;justify-content:center}
.contact h3{left:94px;top:183px;font-size:31px;color:var(--purple-light)}
.contact .uline{left:94px;top:233px;width:140px;height:1px;background:rgba(255,255,255,.35)}
.contact .lead{left:94px;top:250px;width:340px;font-size:14px;line-height:20px;color:var(--muted)}
.form-box{left:683px;top:42px;width:327px;height:332px;background:#050505;border:4px solid var(--purple-light)}
.field{position:absolute;left:26px;width:276px;height:36px;background:var(--white);font-size:13px;color:#777;padding:8px 6px}
.form-box .submit{position:absolute;left:57px;top:264px;width:210px;height:36px;background:var(--purple);color:var(--white);font-size:15px;display:flex;align-items:center;justify-content:center}

/* services */
.services{top:1502px;height:627px;background:linear-gradient(180deg,#f4f4f4,#e4e4e4)}
.services h2{position:absolute;top:26px;width:100%;text-align:center;font-size:33px;line-height:40px;color:#2b2b2b}
.bulb{left:468px;top:112px;width:262px;height:468px;border-radius:130px 130px 60px 60px;background:radial-gradient(ellipse at 50% 35%,#ffffff 0%,#eae7e2 50%,#b9b3a9 100%)}
.service{position:absolute;width:270px;text-align:center}
.service .ic{width:86px;height:86px;margin:0 auto;border:3px solid var(--purple);border-radius:50%;display:flex;align-items:center;justify-content:center;background:rgba(255,255,255,.6)}
.service h4{font-size:18px;font-weight:600;color:#222;margin-top:6px}
.service p{font-size:14px;line-height:19px;color:#444}

/* testimonials */
.testimonials{top:2129px;height:484px;background:linear-gradient(135deg,#7b3bbd,#5a2398)}
.testimonials h2{position:absolute;top:22px;width:100%;text-align:center;font-size:33px;color:var(--white)}
.quote{position:absolute;font-size:14px;line-height:22px;padding:30px 24px}
.quote.light{left:68px;top:138px;width:503px;height:173px;background:var(--white);color:#333}
.quote.dark{left:575px;top:159px;width:503px;height:129px;background:#1c1722;color:var(--white);display:flex;align-items:center;justify-content:center}
.tail{position:absolute;width:0;height:0;border-left:14px solid transparent;border-right:14px solid transparent}
.avatar{position:absolute;width:102px;height:102px;border-radius:50%;border:3px solid var(--white);background:radial-gradient(circle at 50% 40%,#d9b79b,#5b3a2a)}
.person{position:absolute;color:var(--white)}
.person b{display:block;font-size:16px}
.person span{font-size:12px}

/* newsletter */
.newsletter{top:2613px;height:381px;background:linear-gradient(180deg,#fafafa,#eeeeee)}
.newsletter h2{position:absolute;top:34px;width:100%;text-align:center;font-size:33px;color:#111}
.email-in{left:168px;top:142px;width:838px;height:66px;border:2px solid var(--purple-light);border-radius:6px;background:var(--white);font-size:16px;color:#333;padding:22px 24px}
.btn-sub{left:475px;top:245px;width:227px;height:63px;background:var(--purple);color:var(--white);border-radius:4px;font-size:18px;display:flex;align-items:center;justify-content:center}

/* info */
.info{top:2994px;height:451px;background:var(--night)}
.info h3{left:77px;top:40px;font-size:31px;color:var(--purple-light)}
.info .uline{left:77px;top:98px;width:140px;height:1px;background:rgba(255,255,255,.35)}
.info-row{position:absolute;left:80px;display:flex;gap:20px;color:var(--white);font-size:15px;line-height:22px}
.info-row .dot{width:24px;height:24px;border-radius:50%;background:#d9d9d9;flex:none;display:flex;align-items:center;justify-content:center;margin-top:2px}
.follow{left:82px;top:334px;color:var(--white);font-size:22px}
.social{position:absolute;top:384px;width:30px;height:30px;background:var(--white);transform:rotate(45deg)}
.info h3.loc{left:625px;top:32px;color:var(--white)}
.map{left:627px;top:94px;width:414px;height:339px;border:6px solid var(--purple-light);background:linear-gradient(135deg,#e9e4d8,#d8d2c4 60%,#e9c98a)}

.footer{position:absolute;left:0;top:3445px;width:1200px;height:64px;background:var(--footer);color:var(--white);font-size:14px;display:flex;align-items:center;justify-content:center;text-align:center}
</style>
</head>
<body>

<section class="hero">
  <div class="abs hero-photo" role="img" aria-label="Dark photo of glowing fibre optic strands"></div>
  <svg class="abs" style="left:0;top:0" width="1200" height="604" aria-hidden="true">
    <defs><linearGradient id="heroPurple" x1="0" y1="0" x2="1" y2="1"><stop offset="0" stop-color="#5a1f96"/><stop offset="1" stop-color="#7a3cc0"/></linearGradient></defs>
    <polygon points="877,0 1200,0 1200,604 678,604" fill="url(#heroPurple)"/>
  </svg>
  <div class="abs nav-logo heading">K7</div>
  <nav class="abs nav">
    <a class="active" style="left:438px">Home</a>
    <a style="left:528px">About</a>
    <a style="left:625px">Gallery</a>
    <a style="left:735px">Contact Us</a>
    <a class="phone">
      <svg width="16" height="16" viewBox="0 0 24 24"><path fill="#fff" d="M6.6 10.8a15 15 0 0 0 6.6 6.6l2.2-2.2c.3-.3.7-.4 1-.2 1.1.4 2.3.6 3.6.6.6 0 1 .4 1 1V20c0 .6-.4 1-1 1A17 17 0 0 1 3 4c0-.6.4-1 1-1h3.5c.6 0 1 .4 1 1 0 1.3.2 2.5.6 3.6.1.3 0 .7-.2 1z"/></svg>
      + (1800) - 402 - 517</a>
  </nav>
  <h1 class="abs hero-title heading">RESIDENTIAL<br><span>ELECTRICAL SERVICES</span></h1>
  <p class="abs hero-text">We do fast phone repair. In most cases, technicians will be able to repair your device in just minutes,</p>
  <div class="abs btn-learn">Learn More</div>
  <div class="abs hero-logo">K7 Electrical<br>Services Ltd</div>
</section>

<section class="about">
  <div class="mark-row" style="top:62px"><span class="rule"></span><span class="mark">K7</span><span class="rule"></span></div>
  <h2 class="heading">K7 ELECTRICAL SERVICES</h2>
  <div class="divider"></div>
  <p>Lorem Ipsum has been the industry's standard dummy text ever since the 1500s, when an unknown printer took a galley of type and scrambled it to make a type specimen book. It has survived not only five centuries, but also the leap into electronic typesetting, remaining essentially unchanged.</p>
  <div class="btn-outline">READ MORE</div>
  <div class="callus"><b>CALL US</b> <svg width="18" height="18" viewBox="0 0 24 24" style="vertical-align:-3px"><circle cx="12" cy="12" r="11" fill="none" stroke="#6c2fab" stroke-width="2"/><path fill="#6c2fab" d="M8.5 10.8a8 8 0 0 0 4.7 4.7l1.3-1.3c.2-.2.4-.2.6-.1.6.2 1.2.3 1.8.3v2.1c0 .3-.2.5-.5.5A9 9 0 0 1 7 7.6c0-.3.2-.5.5-.5h2.1c0 .6.1 1.2.3 1.8.1.2 0 .4-.1.6z"/></svg> 555-318-2046</div>
</section>

<section class="contact">
  <svg class="abs" style="left:0;top:0" width="1200" height="414" aria-hidden="true">
    <polygon points="585,0 1200,0 1200,414 416,414" fill="#6a2ca8"/>
  </svg>
  <div class="abs contact-icon">
    <svg width="38" height="38" viewBox="0 0 24 24" fill="none" stroke="#fff" stroke-width="1.6"><rect x="5" y="3" width="14" height="18" rx="1.5"/><path d="M8 8h8M8 12h8M8 16h5"/></svg>
  </div>
  <h3 class="abs heading">CONTACT FROM</h3>
  <div class="abs uline"></div>
  <p class="abs lead">Lorem Ipsum has been the industry's standard dummy text ever since the 1500s,</p>
  <div class="abs form-box">
    <div class="field" style="top:21px">*Name</div>
    <div class="field" style="top:73px">*Email Address</div>
    <div class="field" style="top:124px">*Phone</div>
    <div class="field" style="top:176px;height:75px">*Message</div>
    <div class="submit">SUBMIT</div>
  </div>
</section>

<section class="services">
  <div class="abs" style="left:0;top:0;width:1200px;height:627px;background:linear-gradient(90deg,rgba(200,200,200,.35),rgba(255,255,255,0) 30%,rgba(255,255,255,0) 70%,rgba(200,200,200,.35))" role="img" aria-label="Faded background photo of electrical wiring"></div>
  <h2 class="heading">OUR SERVICES</h2>
  <div class="mark-row" style="top:74px"><span class="rule" style="width:120px"></span><span class="mark" style="font-size:24px;color:#444">K7</span><span class="rule" style="width:120px"></span></div>
  <div class="abs bulb" role="img" aria-label="Photo of a clear filament light bulb"></div>

  <div class="service" style="left:164px;top:110px">
    <div class="ic"><svg width="44" height="44" viewBox="0 0 24 24" fill="none" stroke="#6c2fab" stroke-width="1.6"><path d="M7 4h10l2 9H5z"/><path d="M12 13v6M8 20h8"/></svg></div>
    <h4>Electrical</h4><p>Lorem Ipsum has been the industry's standard dummy text ever</p>
  </div>
  <div class="service" style="left:68px;top:271px">
    <div class="ic"><svg width="44" height="44" viewBox="0 0 24 24" fill="none" stroke="#6c2fab" stroke-width="1.6"><rect x="6" y="6" width="12" height="12"/><rect x="9" y="9" width="6" height="6"/><path d="M9 3v3M12 3v3M15 3v3M9 18v3M12 18v3M15 18v3M3 9h3M3 12h3M3 15h3M18 9h3M18 12h3M18 15h3"/></svg></div>
    <h4>Panels Changes</h4><p>Lorem Ipsum has been the industry's standard dummy text ever</p>
  </div>
  <div class="service" style="left:192px;top:440px">
    <div class="ic"><svg width="44" height="44" viewBox="0 0 24 24" fill="none" stroke="#6c2fab" stroke-width="1.6"><path d="M3 8l14-3 2 6-14 3z"/><path d="M9 13l1 4H4M19 8h2"/></svg></div>
    <h4>Security Systems</h4><p>Lorem Ipsum has been the industry's standard dummy text ever</p>
  </div>
  <div class="service" style="left:768px;top:110px">
    <div class="ic"><svg width="44" height="44" viewBox="0 0 24 24" fill="none" stroke="#6c2fab" stroke-width="1.6"><rect x="4" y="7" width="16" height="13" rx="1"/><path d="M8 7v13M12 7v13M16 7v13M8 2c1 1-1 2 0 3M12 2c1 1-1 2 0 3M16 2c1 1-1 2 0 3"/></svg></div>
    <h4>Heating</h4><p>Lorem Ipsum has been the industry's standard dummy text ever</p>
  </div>
  <div class="service" style="left:866px;top:271px">
    <div class="ic"><svg width="44" height="44" viewBox="0 0 24 24" fill="none" stroke="#6c2fab" stroke-width="1.6"><rect x="4" y="4" width="16" height="16" rx="1"/><path d="M8 7v10M11 7v10M14 7v10M17 7v10"/></svg></div>
    <h4>Air Conditioning</h4><p>Lorem Ipsum has been the industry's standard dummy text ever</p>
  </div>
  <div class="service" style="left:740px;top:435px">
    <div class="ic"><svg width="44" height="44" viewBox="0 0 24 24" fill="none" stroke="#6c2fab" stroke-width="1.8"><path d="M4 20l9-9M14 4a4 4 0 0 0 5 5l-3 3-5-5zM20 20L9 9M5 4l2 2-1 1-2-2z"/></svg></div>
    <h4>Trouble Shooting</h4><p>Lorem Ipsum has been the industry's standard dummy text ever</p>
  </div>
</section>

<section class="testimonials">
  <h2 class="heading">OUR TESTIMONIALS</h2>
  <div class="mark-row on-dark" style="top:76px"><span class="rule" style="width:120px"></span><span class="mark" style="font-size:28px">K7</span><span class="rule" style="width:120px"></span></div>
  <div class="quote light">Lorem ipsum dolor sit amet, consectetur adipisicing elit, sed do eiusmod tempor incididunt ut labore et dolore magna aliqua. Ut enim ad minim veniam, quis nostrud exercitation ullamco laboris nisi ut aliquip ex ea commodo consequat. Duis aute irure dolor.</div>
  <div class="tail" style="left:190px;top:311px;border-top:18px solid #fff"></div>
  <div class="quote dark">These guys solved my problem in a moment. Highly recommended!</div>
  <div class="tail" style="left:925px;top:288px;border-top:18px solid #1c1722"></div>
  <div class="avatar" style="left:157px;top:347px" role="img" aria-label="Customer portrait photo"></div>
  <div class="person" style="left:271px;top:368px"><b>Jane Doe</b><span>Engineer of Media Production</span></div>
  <div class="avatar" style="left:908px;top:332px" role="img" aria-label="Customer portrait photo"></div>
  <div class="person" style="left:690px;top:347px;width:200px;text-align:right"><b>Jane Doe</b><span>Engineer of Media Production</span></div>
</section>

<section class="newsletter">
  <h2 class="heading">Subscribe To Our Newsletter :</h2>
  <div class="mark-row" style="top:94px"><span class="rule" style="width:190px;background:#999"></span><span class="mark" style="font-size:28px">K7</span><span class="rule" style="width:190px;background:#999"></span></div>
  <div class="abs email-in">Enter Your Email</div>
  <div class="abs btn-sub">SUBMIT</div>
</section>

<section class="info">
  <svg class="abs" style="left:0;top:0" width="1200" height="451" aria-hidden="true">
    <polygon points="589,0 1200,0 1200,451 421,451" fill="#6a2ca8"/>
  </svg>
  <h3 class="abs heading">CONTACT INFORMATION</h3>
  <div class="abs uline"></div>
  <div class="info-row" style="top:144px">
    <span class="dot"><svg width="12" height="12" viewBox="0 0 24 24"><path fill="#1a0f27" d="M12 2a7 7 0 0 0-7 7c0 5 7 13 7 13s7-8 7-13a7 7 0 0 0-7-7zm0 9.5A2.5 2.5 0 1 1 12 6.5a2.5 2.5 0 0 1 0 5z"/></svg></span>
    <span>Level 4, Suite 7<br>88 Harbourline Road<br>Westbank, Victoria 3910</span>
  </div>
  <div class="info-row" style="top:227px">
    <span class="dot"><svg width="12" height="12" viewBox="0 0 24 24"><path fill="#1a0f27" d="M6.6 10.8a15 15 0 0 0 6.6 6.6l2.2-2.2c.3-.3.7-.4 1-.2 1.1.4 2.3.6 3.6.6.6 0 1 .4 1 1V20c0 .6-.4 1-1 1A17 17 0 0 1 3 4c0-.6.4-1 1-1h3.5c.6 0 1 .4 1 1 0 1.3.2 2.5.6 3.6.1.3 0 .7-.2 1z"/></svg></span>
    <span>+61 3 5550 2731</span>
  </div>
  <div class="info-row" style="top:281px">
    <span class="dot"><svg width="12" height="12" viewBox="0 0 24 24"><path fill="#1a0f27" d="M3 5h18v14H3zm2 2v.5l7 5 7-5V7z"/></svg></span>
    <span>hello@k7electrical.example</span>
  </div>
  <div class="abs follow">Follow us on</div>
  <span class="social" style="left:94px"></span>
  <span class="social" style="left:138px"></span>
  <span class="social" style="left:182px"></span>
  <span class="social" style="left:226px"></span>
  <h3 class="abs heading loc">OUR LOCATION</h3>
  <div class="abs map" role="img" aria-label="Street map showing the office location"></div>
</section>

<footer class="footer">Copyright © 2007 - 2018 Electric Company Contractors, licenses number 40917362 Inc. All Rights Reserved</footer>

</body>
</html>
```